Design (no text) for 7 pages of Wordpress website

I need seven of the pages on a website re-designed. The website is using Wordpress as the platform.

The text on the pages can remain unchanged.

The site is for outdoor markets, events.

Industry/Entity Type

Events, markets, fairs

Number of Pages Required

5+ page

Colors
00AB8E
00BBA5
67D7C9
C6EFE9
E9F9F6
EE7325
F08F49
F5BC92
FAE3D3
FDF4ED

```html
<!DOCTYPE html>
<html lang="en">
<head>
<meta charset="utf-8">
<title>Gecko Grove Markets – Visitor and Stallholder Pages</title>
<link href="https://fonts.googleapis.com/css2?family=Lato:ital,wght@0,400;0,700;0,900;1,400&display=swap" rel="stylesheet">
<style>
:root{
  --teal:#00AB8E;
  --teal-bright:#16B396;
  --mint:#E9F9F6;
  --orange:#EE7325;
  --orange-soft:#F08F49;
  --peach:#F5BC92;
  --cream:#FDF4ED;
  --stage:#DA5A22;
  --ink:#1e1e1e;
  --body:#3a3a3a;
  --rule:#dcdcdc;
  --footer:#1b1b1b;
  --white:#ffffff;
}
*{margin:0;padding:0;box-sizing:border-box}
html,body{width:1200px;height:2200px;overflow:hidden}
body{background:var(--stage);font-family:"Lato",Arial,sans-serif;color:var(--body);position:relative}
ul{list-style:none}

.page{position:absolute;top:59px;width:520px;background:var(--white);overflow:hidden}
.page--visitor{left:65px;height:1120px}
.page--stallholder{left:618px;height:2081px}

/* top bar */
.topbar{height:23px;background:var(--mint);display:flex;align-items:center;padding:0 31px;font-size:6.6px;color:var(--teal);font-weight:700}
.topbar .sep{color:var(--ink);margin:0 7px;font-weight:400}
.topbar svg{margin-right:5px}
.search{margin-left:auto;width:90px;border-bottom:1px solid var(--orange);display:flex;justify-content:space-between;align-items:center;color:var(--ink);font-weight:400;padding-bottom:1px}

/* nav */
.nav{height:44px;display:flex;align-items:center;padding:0 27px}
.brand{display:flex;align-items:center;gap:4px;font-weight:900;font-size:11.5px;color:var(--ink);letter-spacing:-.2px;width:72px}
.brand-mark{width:7px;height:7px;background:var(--orange)}
.menu{display:flex;gap:16px;margin-left:26px;font-size:5.6px;font-weight:700;color:var(--ink)}
.menu .active{color:var(--teal)}

/* hero */
.hero{height:140px;position:relative;background:linear-gradient(100deg,#4a4c55 0%,#6d6462 35%,#7f7670 60%,#535a63 100%)}
.hero-title{position:absolute;left:31px;top:60px;color:var(--white);font-size:15px;font-weight:700;text-shadow:0 1px 2px rgba(0,0,0,.4)}
.hero-card{position:absolute;left:327px;top:14px;width:161px;height:112px;background:rgba(238,115,37,.92);border-radius:3px;padding:12px 12px;color:var(--white)}
.hero-card h3{font-size:11px;font-weight:700;margin-bottom:9px}
.hero-card p{font-size:6.6px;line-height:1.6;margin-bottom:4px}

/* photo blocks */
.photo{position:absolute;width:215px;height:169px}
.photo::before{content:"";position:absolute;left:18px;right:-7px;top:-7px;bottom:7px;background:var(--teal-bright);border-radius:3px}
.photo-fill{position:absolute;inset:0;border-radius:4px}

/* text */
h2{color:var(--ink);font-size:15px;font-weight:700;line-height:1.22}
.copy p{font-size:5.9px;line-height:1.9;margin-bottom:4px}
.section{position:relative;overflow:hidden}
.ruled{border-top:1px solid var(--rule)}

.intro{height:245px}
.intro .copy{position:absolute;left:31px;top:29px;width:226px}
.intro h2{margin-bottom:10px}

.features{height:335px;background:var(--cream);text-align:center;padding-top:30px}
.features .lead{font-size:9px;color:var(--ink);margin-bottom:5px}
.features .sub{font-size:9.6px;color:var(--teal);font-weight:700}
.grid{display:grid;grid-template-columns:repeat(3,148px);column-gap:8px;justify-content:center}
.feature{text-align:center}
.feature .icon{width:30px;height:30px;margin:0 auto 7px;border-radius:4px;background:var(--peach)}
.feature h4{font-size:8.6px;color:var(--orange);font-weight:700;margin-bottom:5px}
.feature p{font-size:5.8px;line-height:2;color:var(--body)}
.features .grid{margin-top:16px;row-gap:18px}

.family{height:263px}
.family .copy{position:absolute;left:31px;top:24px;width:226px}
.family h2{margin-bottom:5px}
.family .copy p{margin-bottom:1px;line-height:1.95}
.note{position:absolute;left:31px;top:222px;font-size:5.9px;font-style:italic;color:var(--orange);line-height:2.1}

.footer{height:70px;background:var(--footer);text-align:center;color:var(--white);padding-top:23px}
.footer p{font-size:5.4px;margin-bottom:6px}
.social{display:flex;gap:9px;justify-content:center}
.social span{width:8px;height:8px;border-radius:50%;background:var(--white)}

/* tick list */
.ticks li{position:relative;padding-left:14px;font-size:6.3px;line-height:1.7;margin-bottom:4.3px;color:var(--body)}
.ticks li::before{content:"";position:absolute;left:0;top:1.6px;width:7px;height:7px;border-radius:50%;background:var(--orange)}
.ticks li::after{content:"";position:absolute;left:2.5px;top:2.7px;width:1.8px;height:3.2px;border:solid var(--white);border-width:0 1px 1px 0;transform:rotate(45deg)}

/* stallholder page */
.welcome{height:325px;text-align:center}
.welcome h2{font-size:15.5px;padding-top:27px;margin-bottom:12px}
.welcome .copy p{font-size:6.4px;line-height:2;margin-bottom:0}
.welcome .ticks{position:absolute;left:33px;top:120px;width:212px;text-align:left}

.block{padding:16px 33px 0}
.block h3{font-size:12.4px;color:var(--ink);font-weight:700;margin-bottom:8px}
.block .ticks li{margin-bottom:6px}
.placement{height:133px}
.entry{height:127px}
.entry .cols{display:flex}
.entry .col{width:236px}
.entry .col + .col{width:260px}
.entry .small{font-size:6.3px;line-height:1.7;margin-top:-2px}
.entry .alert{font-size:6.2px;font-weight:700;color:var(--ink);margin-top:14px;white-space:nowrap}
.prebook{height:218px}
.food{height:133px}
.food p{font-size:6.3px;line-height:1.9;margin-bottom:5px}

.idea{height:376px;background:var(--cream);text-align:center;padding-top:24px}
.idea h2{font-size:13.4px;font-weight:400;color:var(--ink);margin-bottom:8px}
.idea .copy{width:410px;margin:0 auto}
.idea .copy p{font-size:6.3px;line-height:2;margin-bottom:0}
.idea .grid{margin-top:16px;row-gap:16px;grid-template-columns:repeat(3,148px);column-gap:10px}

.banned{height:335px;padding-top:16px}
.banned h2{text-align:center;font-size:15px;margin-bottom:20px}
.banned .ticks{position:absolute;left:33px;top:62px;width:215px}
.banned .ticks li{margin-bottom:5.5px}

.callout{height:157px;background:var(--teal-bright);color:var(--white);text-align:center;padding-top:24px}
.callout h2{color:var(--white);font-size:15px;margin-bottom:14px}
.callout p{font-size:6.5px;line-height:2}
.callout .strong{font-weight:700;font-size:7px;margin-top:6px}
</style>
</head>
<body>

<!-- Visitor information page -->
<main class="page page--visitor">
  <div class="topbar">
    <svg width="6" height="7" viewBox="0 0 6 7"><path d="M1 0.5 L2.4 0.5 L2.8 2 L2 2.6 Q2.6 4 3.6 4.6 L4.2 3.8 L5.6 4.3 L5.6 5.8 Q2.8 6.6 1 3.6 Q0.2 2 1 0.5Z" fill="#1e1e1e"/></svg>
    Call Us: (02) 5550 1234<span class="sep">/</span>
    <svg width="7" height="5" viewBox="0 0 7 5"><rect width="7" height="5" fill="#1e1e1e"/><path d="M0 0 L3.5 2.6 L7 0" stroke="#fff" stroke-width=".6" fill="none"/></svg>
    hello@marketyard.com.au
    <div class="search">Search <svg width="6" height="6" viewBox="0 0 6 6"><circle cx="2.5" cy="2.5" r="1.8" stroke="#EE7325" fill="none" stroke-width=".9"/><line x1="3.8" y1="3.8" x2="5.6" y2="5.6" stroke="#EE7325" stroke-width="1"/></svg></div>
  </div>
  <nav class="nav">
    <div class="brand"><span class="brand-mark"></span>MARKETYARD</div>
    <ul class="menu"><li>HOME</li><li>BOOK A STALL</li><li>STALLFINDER</li><li class="active">GECKO GROVE MARKETS</li><li>NORTHFIELD MARKETS</li><li>CONTACT US</li><li>ABOUT US</li></ul>
  </nav>
  <header class="hero" role="img" aria-label="Photo of a busy outdoor market with shoppers among stall tents">
    <h1 class="hero-title">Gecko Grove Markets Visitor Info</h1>
    <div class="hero-card">
      <h3>Every Saturday</h3>
      <p>9am-2pm</p>
      <p>Gecko Grove – Westvale Parklands</p>
      <p>Cnr of the Hensley Dr and Copperfield Rd, Ashbury Vale</p>
    </div>
  </header>

  <section class="section intro">
    <div class="copy">
      <h2>Love a Good Saturday<br>Market?</h2>
      <p>Then you need to go to the Gecko Grove Markets.<br>Are markets your idea of fun? Want to take the family somewhere that is rich in culture, choice and variety every week of the year?</p>
      <p>Uncover the secret gem of the Westvale Parklands of Ashbury Vale. Set in lush surroundings in a hub of activity and entertainment are variety goods galore. There’s a wonderful selection of fashion, household items, homewares, handmade craft items and more awaiting you.</p>
      <p>Plus, you’ll find a feast of farm fresh produce, artisan foods and all kinds of eclectic favourites in the one place. We attract family favourites across Asian, Middle Eastern and European cuisines and bring them together with products direct from the producers of Westvale.</p>
    </div>
    <div class="photo" style="left:266px;top:38px">
      <div class="photo-fill" role="img" aria-label="Photo of a crowded evening market lane with festoon lights" style="background:linear-gradient(180deg,#c9ccd3 0%,#9ea3a0 40%,#5f6a55 70%,#4a4640 100%)"></div>
    </div>
  </section>

  <section class="section features">
    <p class="lead">This is a place for you to meet, eat and find a special treat all at the Gecko Grove Markets!</p>
    <p class="sub">What you can expect at the Gecko Grove:</p>
    <div class="grid">
      <div class="feature"><div class="icon" role="img" aria-label="Coffee cup icon"></div><h4>Food &amp; Coffee</h4><p>Grab a bite and a coffee before, during or after your shopping.We’ll have a variety of cuisines and coffee choices available, so you can try something different each week!</p></div>
      <div class="feature"><div class="icon" role="img" aria-label="Kids clothing icon"></div><h4>Kid’s Fashion</h4><p>Shop until you drop at Westvale’s newest kid’s clothing location. Forget running all over town or paying hipster chic prices. Find your kid’s fashion here.</p></div>
      <div class="feature"><div class="icon" role="img" aria-label="Craft hands icon"></div><h4>Get Crafty</h4><p>Nothing beats the beauty and design of quality handmade items. Uncover arts and crafts for all occasions, lovingly made knitwear, patchwork and more.</p></div>
      <div class="feature"><div class="icon" role="img" aria-label="Pet icon"></div><h4>Pet Friendly</h4><p>Bring your furry friends for a frolick through the sprawling Westvale Parklands, while picking up a treat from one of the pet stalls.</p></div>
      <div class="feature"><div class="icon" role="img" aria-label="Child icon"></div><h4>Fun for the kids</h4><p>Bring the kids to enjoy pony rides, a jumping castle and face painting every Saturday.</p></div>
      <div class="feature"><div class="icon" role="img" aria-label="Produce bowl icon"></div><h4>Gourmet Produce</h4><p>Shop a range of quality, gourmet produce and baked goods from olives and preserved lemons, to breads and brownies.</p></div>
    </div>
  </section>

  <section class="section family">
    <div class="copy">
      <h2>We are family-friendly fun</h2>
      <p>Where else can you meet your neighbours, find items at op shop prices, meet the farmer and the food maker, all while keeping the whole family entertained?</p>
      <p>Our markets held in the glorious Westvale Parklands, an oasis of greenery and community in the City of Fairmont. You can spend the day browsing fashion, handmade craft items, bric-a-brac, toys, fantastic produce and food from around the globe. Op shop through items new and old with your family every weekend.</p>
      <p>It’s an ever-changing variety of options. 50% of our market stalls change on a week by week basis, so you can always find a new treasure.</p>
      <p>The Westvale Parklands are there for you to enjoy. There’s live entertainment, special events, food festivals and more held on the grounds. You can come for the op shopping and retail therapy and picnic and relax later with a stroll about the Parklands.</p>
    </div>
    <div class="photo" style="left:266px;top:35px">
      <div class="photo-fill" role="img" aria-label="Photo of a group of friends giving high fives on a city street" style="background:linear-gradient(160deg,#b9c4cf 0%,#8e7f74 45%,#6e5a52 75%,#3f3a3c 100%)"></div>
    </div>
    <p class="note">Gecko Grove markets are open every Saturday from 9am to 2pm.<br>Enter via Copperfield Rd and the Hensley Drive for parking.&nbsp; / &nbsp;Public transport is available via a bus stop at the Gecko Grove entrance.</p>
  </section>

  <footer class="footer">
    <p>Copyright © 2021 Company Name All Rights Reserved</p>
    <div class="social"><span></span><span></span><span></span><span></span><span></span></div>
  </footer>
</main>

<!-- Casual stallholder page -->
<main class="page page--stallholder">
  <div class="topbar">
    <svg width="6" height="7" viewBox="0 0 6 7"><path d="M1 0.5 L2.4 0.5 L2.8 2 L2 2.6 Q2.6 4 3.6 4.6 L4.2 3.8 L5.6 4.3 L5.6 5.8 Q2.8 6.6 1 3.6 Q0.2 2 1 0.5Z" fill="#1e1e1e"/></svg>
    Call Us: (02) 5550 1234<span class="sep">/</span>
    <svg width="7" height="5" viewBox="0 0 7 5"><rect width="7" height="5" fill="#1e1e1e"/><path d="M0 0 L3.5 2.6 L7 0" stroke="#fff" stroke-width=".6" fill="none"/></svg>
    hello@marketyard.com.au
    <div class="search">Search <svg width="6" height="6" viewBox="0 0 6 6"><circle cx="2.5" cy="2.5" r="1.8" stroke="#EE7325" fill="none" stroke-width=".9"/><line x1="3.8" y1="3.8" x2="5.6" y2="5.6" stroke="#EE7325" stroke-width="1"/></svg></div>
  </div>
  <nav class="nav">
    <div class="brand"><span class="brand-mark"></span>MARKETYARD</div>
    <ul class="menu"><li>HOME</li><li>BOOK A STALL</li><li>STALLFINDER</li><li class="active">GECKO GROVE MARKETS</li><li>NORTHFIELD MARKETS</li><li>CONTACT US</li><li>ABOUT US</li></ul>
  </nav>
  <header class="hero" role="img" aria-label="Photo of shoppers walking past market stalls and food vans">
    <h1 class="hero-title">Gecko Grove Markets Casual Stallholder Info</h1>
  </header>

  <section class="section welcome">
    <h2>Home made? Hand made? Collectables or produce?<br>We have got the market for you.</h2>
    <div class="copy">
      <p>Try your luck as a casual stallholder at Gecko Grove Markets in Ashbury Vale.</p>
      <p>Whether you are new to running a market stall, or running your market stall is your bread and butter income,<br>Gecko Grove Markets welcomes you.</p>
    </div>
    <ul class="ticks">
      <li>Book before 5pm the day before to secure your stall</li>
      <li>Or queue up on the day</li>
      <li>Enter via the Eastern Carpark, first left from the Gecko Grove Main Entrance</li>
      <li>Bump in between 7am-9am.</li>
      <li>$40 fee for standard size stalls.</li>
      <li>Approx 5m width x 5m depth.</li>
      <li>Parking for a standard car, van or ute within your stall space is included.</li>
      <li>$75 fee for double stalls.</li>
      <li>Approx 10m width x 5m depth.</li>
      <li>Parking for a car and trailer or small truck within you stall space is included</li>
    </ul>
    <div class="photo" style="left:266px;top:132px">
      <div class="photo-fill" role="img" aria-label="Photo of vintage collectables on an old shelf against a grey wall" style="background:linear-gradient(170deg,#d8d8d6 0%,#b9b6b2 45%,#8a6a52 75%,#6b4c3a 100%)"></div>
    </div>
  </section>

  <section class="section block placement ruled">
    <h3>Stall Placement</h3>
    <ul class="ticks">
      <li>Casual stalls are allocated on a “first come, first served” basis- so be early to secure your spot!</li>
      <li>Our staff are available to help guide you to your casual stallholder allocated space</li>
      <li>As a casual stallholder, you will be allocated the next available spot</li>
      <li>For the safety of patrons, vehicles are not permitted to move within the market ground between 9:00am and 12:00pm<br>unless otherwise stated.</li>
    </ul>
  </section>

  <section class="section block entry ruled">
    <div class="cols">
      <div class="col">
        <h3>Stallholder Entry</h3>
        <ul class="ticks"><li>7:00am-9:00am</li></ul>
        <p class="small">Stallholders are permitted to leave from 12pm if it’s safe<br>enough to do so</p>
      </div>
      <div class="col">
        <h3>Casual Stallholder Exit</h3>
        <ul class="ticks">
          <li>Pre-booked casual stallholders can exit from midday if it is safe to do so</li>
          <li>All other casual stallholders can exit from midday if it is safe to do</li>
          <li>Officially the markets run until 2pm</li>
        </ul>
      </div>
    </div>
    <p class="alert">DURING ANY EXIT: For the safety of market goers and other stallholders, please wait for the advice and assistance of Gecko Grove Market staff before</p>
  </section>

  <section class="section block prebook ruled">
    <h3>Pre-Booking</h3>
    <ul class="ticks">
      <li>Bookings available until 5:00pm the day before the market. This booking can be placed by phone or online.</li>
      <li>To enter the Gecko Grove Market as a pre-booked stallholder, enter via the Eastern Carpark, first left from the Gecko Grove Main Entrance</li>
      <li>Entry from 07:00am-09:00am.</li>
      <li>$40 for standard size stalls. A standard stall includes a parking space for one standard car, van or ute. Approximately 5 meters width x 5 meters depth vacant selling space alongside your vehicle. A standard stall provides approximately enough space for one 3m x 3m marquee, two trestle tables frontage and two clothing racks (for example).</li>
      <li>$75 for a double stall. A large stall includes a parking space for one standard car, van or ute, with a trailer attached, or one truck. Approximately 10 meters width x 5 meters depth vacant selling space alongside your vehicle. A large stall provides approximately enough space for two marquees, four trestle tables frontage and two clothing racks (for example).</li>
      <li>There are no extra fees for insurance.</li>
      <li>Equipment is not included in the stall price. Equipment can be hired separately or provided by the stallholder.</li>
    </ul>
  </section>

  <section class="section block food ruled">
    <h3>Food/Drink Stalls</h3>
    <p>All food/drink stalls who prepare and/or cook food and drink on-site are required to be compliant with State Food Authority and local council regulations and must hold the following</p>
    <p>A current Food Safety Supervisor Certificate</p>
    <p>Current public liability insurance</p>
    <p>Please note: These regulations do not apply to the sale of pre-packaged baked goods and the like.</p>
  </section>

  <section class="section idea">
    <h2>Got a great idea for a casual market stall?</h2>
    <div class="copy">
      <p>Our team is experienced with helping your market stall adventure go to plan. 50% of our market is made up of eager casual stall holders just like you. You can flirt with selling your items without strings or build a timetable of participation as a casual stallholder that works for you.</p>
      <p>The choice is yours at Gecko Grove Markets. That’s why we offer:</p>
    </div>
    <div class="grid">
      <div class="feature"><div class="icon" role="img" aria-label="Flexibility icon"></div><h4>Flexibility</h4><p>As a casual stallholder, you can pre-book your stall to help your planning OR you can grab the early morning inspiration and queue up on the day.</p></div>
      <div class="feature"><div class="icon" role="img" aria-label="Low risk gauge icon"></div><h4>Low Risk</h4><p>If the market is cancelled due to bad weather, you can also transfer your booking to another date. We make it easy for you to fit to your timetable.</p></div>
      <div class="feature"><div class="icon" role="img" aria-label="Checklist icon"></div><h4>No waiting lists</h4><p>At Gecko Grove Markets, we run our markets without wait lists to ensure everyone feels welcome. Our markets are ready and waiting for when inspiration strikes you.</p></div>
      <div class="feature"><div class="icon" role="img" aria-label="Experiment icon"></div><h4>Experiment with freedom</h4><p>Found a treasure you know the big and little kids alike will adore? Reap the rewards with low risk by testing your next business idea with us.</p></div>
      <div class="feature"><div class="icon" role="img" aria-label="Jacket icon"></div><h4>An eclectic mix</h4><p>Be a part of a kaleidoscope of wonder and ever-changing items. You’ll find vintage fashion, curiosities and collectibles, cucumbers, Cuban food and everything in between here.</p></div>
      <div class="feature"><div class="icon" role="img" aria-label="Joined hands icon"></div><h4>Culture and family</h4><p>There’s a rich array of culture and family to discover at Gecko Grove Markets. This is community in action. Everyone comes together to share, bargain, feed and entertain the family.</p></div>
    </div>
  </section>

  <section class="section banned">
    <h2>The sale of the following items is not permitted:</h2>
    <ul class="ticks">
      <li>Cold Drinks without a food safety supervisor certificate and public liability insurance</li>
      <li>Hot Coffee without a food safety supervisor certificate and public liability insurance</li>
      <li>Any ready-to-eat or hot food without a food safety supervisor certificate and public liability insurance</li>
      <li>Potentially hazardous food (ie requires temperature control) without a food safety supervisor certificate and public liability insurance</li>
      <li>Unpackaged food (ie not sold and served in the supplier’s original package) without a food safety supervisor certificate and public liability insurance</li>
      <li>Pirated software, films and music</li>
      <li>Replica clothing and accessories</li>
      <li>Live animals (including but not limited to puppies, kittens and other pets)</li>
      <li>Proscribed second hand items more than six times a year.</li>
      <li>Proscribed second hand items are those that are at high risk of theft. Please visit the State Office of Fair Trading website for more information</li>
    </ul>
    <div class="photo" style="left:266px;top:63px">
      <div class="photo-fill" role="img" aria-label="Photo of a person in a suit holding up yes and no signs at a desk" style="background:linear-gradient(180deg,#2f3036 0%,#23252c 55%,#6b4b33 78%,#8b6646 100%)"></div>
    </div>
  </section>

  <section class="section callout">
    <h2>Calling All Casual Market Stallholders –<br>The Gecko Grove Markets Wants You!</h2>
    <p>Bring your sense of magic, your great ideas, those treasures you’ve found and more. You are always welcome at the Gecko Grove Markets in<br>Ashbury Vale. We offer causal stall holder spaces for people that want to:</p>
    <p class="strong">Turn that hobby or love of collecting into something that pays for itself through buying and selling<br>Enjoy the casual stallholder status while you try out the market without a big commitment</p>
  </section>

  <footer class="footer">
    <p>Copyright © 2021 Company Name All Rights Reserved</p>
    <div class="social"><span></span><span></span><span></span><span></span><span></span></div>
  </footer>
</main>

</body>
</html>
```